Flyer für Vermietung und Verkauf von Hüpfburgen, aufblasbaren Festzelten und aufblasbaren Hindernisparcours
Flyer für Vermietung und Verkauf von Hüpfburgen, aufblasbaren Festzelten und aufblasbaren Hinder..
Zielgruppe
Wir vermieten und verkaufen Hüpfburgen, aufblasbare Festzelte und aufblasbare Hindernisparcours. Ebenso Sport- und Fungeräte mit Augmented Reality. Für den aktuelen Flyer sollen Vereine, Städte, Gemeinden und Private für den Fasching angesprochen werden.
Aufgabenstellung
Der Flyer soll A4 sein mit 6 Bildern.
Als Text soll enthalten sein:
Slogan: Ihre Faschingsparty mit unseren aufblasbaren Highlights (bessere Ideen sind gerne gefragt)
Text: Machen Sie mit unseren aufblasbaren Hinguckern Ihre Faschingsparty zum absoluten Highlight.
Ganz gleich, ob in der Firma oder privat, für jeden Anlass bieten wir die passende Ergänzung.
Spiele, Hüpfburgen, Sport-Parcours oder Festzelte mit Beleuchtung, wir bieten Ihnen unbegrenzte Möglichkeiten für Ihre Party.
Kontakt:
Bei Interesse kontaktieren Sie uns bitte via Email!
Sabine Krämpel sa.kraempel@blasowind.biz
Seestadt (Germany) - Talheim (Austria)

```html
<!DOCTYPE html>
<html lang="de">
<head>
<meta charset="utf-8">
<title>blasowind – Faschingsflyer</title>
<link rel="stylesheet" href="https://fonts.googleapis.com/css2?family=Montserrat:wght@800&family=Open+Sans:wght@400;600;700&display=swap">
<style>
  :root {
    --page-bg: #e6e7e8;
    --paper: #eeeeef;
    --red: #cf3a3d;
    --navy: #4e5d7d;
    --band-grey: #cfd2d5;
    --ink: #4a4b4d;
    --white: #ffffff;
    --contact-ink: #e9ebf0;
  }
  * { box-sizing: border-box; margin: 0; padding: 0; }
  html, body {
    width: 1200px; height: 1200px; overflow: hidden;
    background: var(--page-bg);
    font-family: "Open Sans", Arial, sans-serif;
  }
  .flyer {
    position: absolute; left: 210px; top: 48px;
    width: 780px; height: 1103px;
    background: var(--paper);
    overflow: hidden;
    box-shadow: 0 6px 24px rgba(0,0,0,.18);
  }
  .brand {
    position: absolute; top: 70px; left: 0; right: 0;
    text-align: center;
  }
  .brand-name {
    display: inline-flex; align-items: center; gap: 14px;
    font-weight: 700; font-size: 46px; color: var(--ink); letter-spacing: .5px;
  }
  .brand-dot { width: 34px; height: 34px; border-radius: 50%; background: var(--red); }
  .brand-tagline {
    margin-top: 8px; font-size: 20px; color: var(--ink); line-height: 1.15;
    text-align: right; width: 300px; margin-left: 360px;
  }
  .hero-visual {
    position: absolute; top: 222px; left: 90px; width: 620px; height: 270px;
    border-radius: 24px;
    background: linear-gradient(90deg, #6dbb3a 0%, #d9c23a 40%, #a3824e 62%, #f4d017 85%, #f2c40d 100%);
  }
  .band-shadow, .band-red {
    position: absolute; left: 58px; right: 0; bottom: 0;
    border-radius: 70px 70px 0 0;
  }
  .band-shadow { top: 560px; background: var(--band-grey); }
  .band-red { top: 580px; background: var(--red); }
  .gallery {
    position: absolute; top: 510px; left: 100px; right: 90px;
    display: flex; justify-content: space-between;
  }
  .photo-frame {
    background: var(--white); padding: 10px;
    box-shadow: 0 4px 12px rgba(0,0,0,.25);
  }
  .photo { display: block; height: 150px; }
  .photo.tower { width: 180px; background: linear-gradient(180deg, #c8453a, #e07a2a 70%, #f0a03a); }
  .photo.slide { width: 130px; background: linear-gradient(180deg, #e03a2e, #f2c51c 60%, #c8342c); }
  .photo.cabin { width: 200px; background: linear-gradient(180deg, #e9e9ea 0%, #8a6a52 40%, #5e4434 100%); }
  .headline {
    position: absolute; top: 730px; left: 80px; right: 30px;
    text-align: center; color: var(--white);
    font-family: "Montserrat", Arial, sans-serif; font-weight: 800;
    font-size: 31px; line-height: 1.2; text-transform: uppercase;
  }
  .body-copy {
    position: absolute; top: 825px; left: 105px; right: 50px;
    text-align: center; color: var(--white);
    font-size: 15px; line-height: 1.75;
  }
  .body-copy strong { font-weight: 700; }
  .footer-bar {
    position: absolute; left: 0; right: 0; bottom: 0; height: 110px;
    background: var(--navy); border-radius: 28px 28px 0 0;
  }
  .cta {
    position: absolute; top: 965px; left: 110px; width: 600px; height: 54px;
    background: var(--red); border-radius: 14px;
    box-shadow: 0 4px 10px rgba(0,0,0,.25);
    color: var(--white); font-weight: 700; font-size: 21px;
    display: flex; align-items: center; justify-content: center;
  }
  .contact {
    position: absolute; bottom: 30px; left: 30px; right: 30px;
    display: flex; justify-content: center; align-items: center; gap: 14px;
    color: var(--contact-ink); font-weight: 700; font-size: 16px;
    white-space: nowrap;
  }
  .contact-sep { width: 6px; height: 6px; border-radius: 50%; background: var(--red); flex: none; }
</style>
</head>
<body>
  <main class="flyer">
    <header class="brand">
      <div class="brand-name"><span class="brand-dot"></span>blasowind</div>
      <p class="brand-tagline">Luft rein –<br>Spaß raus</p>
    </header>

    <div class="hero-visual" role="img" aria-label="Aufblasbares Krokodil, aufblasbare Tiki-Bar und riesige gelbe Gummiente"></div>

    <div class="band-shadow"></div>
    <div class="band-red"></div>

    <section class="gallery">
      <figure class="photo-frame"><span class="photo tower" role="img" aria-label="Aufblasbarer Kletterturm mit Feuerwehrauto"></span></figure>
      <figure class="photo-frame"><span class="photo slide" role="img" aria-label="Aufblasbare Riesenrutsche"></span></figure>
      <figure class="photo-frame"><span class="photo cabin" role="img" aria-label="Aufblasbares Festzelt als Blockhütte"></span></figure>
    </section>

    <h1 class="headline">Ihre Faschingsparty mit unseren<br>aufblasbaren Highlights</h1>

    <p class="body-copy">
      Machen Sie mit unseren aufblasbaren Hinguckern Ihre Faschingsparty zum absoluten
      Highlight. Ganz gleich, ob in der Firma oder privat, für jeden Anlass bieten wir die
      passende <strong>Ergänzung. Spiele, Hüpfburgen, Sport-Parcours oder Festzelte mit
      Beleuchtung</strong>, wir bieten Ihnen unbegrenzte Möglichkeiten für Ihre Party.
    </p>

    <footer class="footer-bar">
      <div class="contact">
        <span>Sabine Krämpel</span><span class="contact-sep"></span>
        <span>sa.kraempel@blasowind.biz</span><span class="contact-sep"></span>
        <span>Seestadt (Germany) - Talheim (Austria)</span>
      </div>
    </footer>

    <div class="cta">Bei Interesse kontaktieren Sie uns bitte via Email!</div>
  </main>
</body>
</html>
```